Campaign Website

I need a website for my judicial campaign. I would like a site that directs from this domain as well as a new domain with my married last name. I need separate pages on the site that address my diversion programs, and a page to allow people to donate with a link to my bank account and a link for people to submit requests to volunteer, get yard signs, etc.

```html
<!DOCTYPE html>
<html lang="en">
<head>
<meta charset="utf-8">
<title>Harper Danielle — Campaign</title>
<link rel="stylesheet" href="https://fonts.googleapis.com/css2?family=Bebas+Neue&family=Montserrat:wght@400;500;600;700&display=swap">
<style>
:root{
  --orange:#ff6a1f;
  --ink:#1c1c1c;
  --text:#333;
  --light:#f3f3f3;
  --white:#fff;
}
*{margin:0;padding:0;box-sizing:border-box}
html,body{width:1200px;height:3405px;overflow:hidden;background:var(--white)}
body{position:relative;font-family:'Montserrat',sans-serif;color:var(--text)}
.abs{position:absolute}
.display{font-family:'Bebas Neue',sans-serif;color:var(--ink);letter-spacing:.5px;line-height:1}
.rule{position:absolute;height:3px;background:var(--ink)}
.btn{position:absolute;border:2px solid var(--ink);display:flex;align-items:center;justify-content:center;font-size:17px;color:var(--ink)}
.slant{position:absolute;left:0;width:1200px}

/* header */
.site-header{position:absolute;left:0;top:0;width:1200px;height:104px;background:var(--white)}
.brand{left:111px;top:34px;font-size:40px}
.nav a{position:absolute;top:0;height:104px;display:flex;align-items:center;font-size:16px;color:var(--ink);text-decoration:none;transform:translateX(-50%)}
.nav a.active{background:var(--orange);color:var(--white);width:90px;justify-content:center;font-weight:600}

/* hero */
.hero{left:0;top:104px;width:1200px;height:592px;background:linear-gradient(90deg,#3d2a1f 0%,#5a3d2b 45%,#6d4a33 70%,#4a3324 100%)}
.hero-title{left:111px;top:262px;font-size:58px;color:var(--white)}
.hero-text{left:111px;top:346px;width:420px;font-size:18px;line-height:33px;color:var(--white)}
.hero .btn,.hero-btn{border-color:var(--white);color:var(--white)}
.arrow{position:absolute;top:336px}

/* biography */
.bio-bg{left:0;top:696px;width:1200px;height:832px;background:var(--light)}
.bio-photo{left:111px;top:818px;width:424px;height:510px;background:linear-gradient(135deg,#6b6b6b,#2b2b2b 60%,#111)}
.frame{position:absolute;border:2px solid var(--ink)}
.bio-copy{left:580px;top:956px;width:436px;font-size:13.4px;line-height:24px;color:var(--text);text-align:justify}
.bio-copy p+p{margin-top:19px}

/* events */
.section-title{left:0;width:1200px;text-align:center;font-size:44px}
.card{position:absolute;top:1718px;width:218px;height:243px;background:var(--white);border-top:5px solid var(--ink);box-shadow:0 2px 8px rgba(0,0,0,.12);text-align:center}
.card.featured{background:var(--orange);border-top-color:var(--light)}
.card svg{margin-top:32px}
.card .num{font-size:54px;font-weight:700;color:var(--ink);line-height:1;margin-top:22px}
.card .label{font-size:17px;color:var(--ink);margin-top:12px}
.card.featured .num,.card.featured .label{color:var(--white)}

/* voting */
.voting{left:0;top:2048px;width:1200px;height:712px;background:linear-gradient(180deg,#2b2b30,#1d1d22 60%,#141417)}
.ring{position:absolute;width:322px;height:322px;border-radius:50%;border:5px solid var(--white);box-shadow:inset 0 0 0 14px rgba(0,0,0,.35);text-align:center;color:var(--white)}
.ring .head{font-family:'Bebas Neue',sans-serif;font-size:28px;position:absolute;left:0;width:100%;top:183px}
.ring .date{font-size:19px;position:absolute;left:0;width:100%;top:222px}

/* donate */
.donate-bg{left:0;top:2733px;width:1200px;height:465px;background:var(--light)}
.donate-text{left:382px;top:2940px;width:780px;font-size:15.5px;line-height:24px;color:var(--text)}

/* footer */
.footer-head{left:172px;top:3248px;font-size:18px;font-weight:700;color:var(--ink)}
.footer-addr{left:172px;top:3284px;font-size:14px;line-height:22.5px;color:var(--ink)}
.social{position:absolute;top:3254px;width:42px;height:42px;border-radius:50%;border:2.5px solid var(--ink)}
.copyright{left:581px;width:507px;top:3343px;text-align:right;font-size:14px;color:var(--ink)}
</style>
</head>
<body>

<!-- header -->
<header class="site-header">
  <div class="abs display brand">HARPER DANIELLE</div>
  <nav class="nav">
    <a class="active" href="#" style="left:638px">Home</a>
    <a href="#" style="left:720px">Pages</a>
    <a href="#" style="left:805px">Biography</a>
    <a href="#" style="left:893px">Events</a>
    <a href="#" style="left:958px">Blog</a>
    <a href="#" style="left:1044px">Contact Us</a>
  </nav>
</header>

<!-- hero -->
<section class="abs hero" role="img" aria-label="Photo of the candidate and her husband embracing in front of a wooden fence"></section>
<svg class="arrow" style="left:40px" width="30" height="46" viewBox="0 0 30 46"><polyline points="26,2 4,23 26,44" fill="none" stroke="#fff" stroke-width="3"/></svg>
<svg class="arrow" style="left:1128px" width="30" height="46" viewBox="0 0 30 46"><polyline points="4,2 26,23 4,44" fill="none" stroke="#fff" stroke-width="3"/></svg>
<h1 class="abs display hero-title">HARPER DANIELLE</h1>
<p class="abs hero-text">Nemo enim ipsam voluptatem quia voluptas sit aspernatur aut odit aut fugit...</p>
<a class="btn hero-btn" style="left:111px;top:437px;width:123px;height:55px">Read More</a>

<!-- biography -->
<div class="abs bio-bg"></div>
<svg class="slant" style="top:610px" height="90" viewBox="0 610 1200 90">
  <polygon points="0,668 1200,696 1200,700 0,700" fill="#f3f3f3"/>
  <polygon points="0,618 820,687 0,668" fill="#ff6a1f"/>
</svg>
<div class="frame" style="left:489px;top:772px;width:598px;height:602px;border-width:4px"></div>
<div class="frame" style="left:506px;top:790px;width:564px;height:566px"></div>
<div class="frame" style="left:523px;top:809px;width:530px;height:528px;border-width:1px"></div>
<div class="abs bio-photo" role="img" aria-label="Portrait of the candidate in a judicial robe in front of flags"></div>
<h2 class="abs display" style="left:580px;top:860px;font-size:40px">BIOGRAPHY</h2>
<div class="rule" style="left:580px;top:922px;width:77px"></div>
<div class="abs bio-copy">
  <p>I was born in Riverton, Kansas, the middle child of five siblings to Leonard and Rosalind Harper. I matriculated at the Eastbrook State University where I received a Bachelor of Arts in Political Science. I earned my Juris Doctorate from the Westfield School of Law where I served as the President of the Black Law Students Association.</p>
  <p>I began my prosecutorial career in Cedar County, TX, where I worked as the Chief Juvenile Prosecutor. I currently work in the Gang Unit as a Felony Assistant District Attorney at the Lakeview County District Attorney's Office.</p>
</div>
<a class="btn" style="left:580px;top:1236px;width:122px;height:54px">Read More</a>

<svg class="slant" style="top:1440px" height="92" viewBox="0 1440 1200 92">
  <polygon points="0,1528 1200,1493 1200,1532 0,1532" fill="#fff"/>
  <polygon points="1200,1443 1200,1493 450,1515" fill="#ff6a1f"/>
</svg>

<!-- events -->
<h2 class="abs display section-title" style="top:1582px">MY EVENTS</h2>
<div class="rule" style="left:561px;top:1647px;width:78px"></div>

<div class="card" style="left:111px">
  <svg width="56" height="56" viewBox="0 0 56 56" fill="none" stroke="#1c1c1c" stroke-width="2.5"><rect x="4" y="8" width="40" height="36" rx="3"/><line x1="4" y1="17" x2="44" y2="17"/><line x1="14" y1="3" x2="14" y2="12"/><line x1="34" y1="3" x2="34" y2="12"/><circle cx="14" cy="26" r="2.5"/><circle cx="24" cy="26" r="2.5"/><circle cx="34" cy="26" r="2.5"/><circle cx="14" cy="35" r="2.5"/><circle cx="24" cy="35" r="2.5"/><circle cx="44" cy="44" r="9" fill="#fff"/><polyline points="39,44 43,48 49,40"/></svg>
  <div class="num">275</div><div class="label">Events</div>
</div>
<div class="card featured" style="left:365px">
  <svg width="56" height="56" viewBox="0 0 56 56" fill="none" stroke="#fff" stroke-width="2.5"><circle cx="28" cy="28" r="18"/><rect x="20" y="24" width="16" height="14" rx="2"/><line x1="24" y1="24" x2="32" y2="16"/><circle cx="6" cy="6" r="4"/><circle cx="50" cy="6" r="4"/><circle cx="6" cy="50" r="4"/><circle cx="50" cy="50" r="4"/><line x1="9" y1="9" x2="15" y2="15"/><line x1="47" y1="9" x2="41" y2="15"/><line x1="9" y1="47" x2="15" y2="41"/><line x1="47" y1="47" x2="41" y2="41"/></svg>
  <div class="num">152</div><div class="label">Campaigns</div>
</div>
<div class="card" style="left:617px">
  <svg width="64" height="56" viewBox="0 0 64 56" fill="none" stroke="#1c1c1c" stroke-width="2.5"><ellipse cx="32" cy="38" rx="29" ry="13"/><circle cx="32" cy="14" r="6"/><circle cx="16" cy="18" r="5"/><circle cx="48" cy="18" r="5"/><path d="M22 34 Q32 20 42 34"/><path d="M6 32 Q14 22 22 30"/><path d="M42 30 Q50 22 58 32"/></svg>
  <div class="num">251</div><div class="label">Meetings</div>
</div>
<div class="card" style="left:870px">
  <svg width="56" height="56" viewBox="0 0 56 56" fill="none" stroke="#1c1c1c" stroke-width="2.5"><circle cx="28" cy="9" r="6"/><path d="M16 26 Q28 12 40 26"/><rect x="10" y="26" width="36" height="26" rx="2"/><circle cx="28" cy="36" r="5"/><path d="M20 50 Q28 40 36 50"/></svg>
  <div class="num">100</div><div class="label">Programmes</div>
</div>

<!-- voting -->
<section class="abs voting" role="img" aria-label="Group photo of supporters gathered in a room with flags"></section>
<svg class="slant" style="top:2040px" height="100" viewBox="0 2040 1200 100">
  <polygon points="0,2040 1200,2040 1200,2075 0,2048" fill="#fff"/>
  <polygon points="560,2088 1200,2075 1200,2136" fill="#ff6a1f"/>
</svg>
<h2 class="abs display section-title" style="top:2175px;color:#fff">VOTING INFORMATION</h2>
<div class="rule" style="left:561px;top:2242px;width:78px;background:#fff"></div>

<div class="ring" style="left:254px;top:2296px">
  <svg style="margin-top:42px" width="90" height="96" viewBox="0 0 90 96" fill="none" stroke="#fff" stroke-width="4"><rect x="40" y="6" width="40" height="30" rx="3" transform="rotate(30 60 21)"/><path d="M26 60 L48 32 L62 44 L44 70 Z"/><line x1="8" y1="90" x2="70" y2="90"/><polyline points="20,90 8,76 26,60"/></svg>
  <div class="head">EARLY VOTING PERIOD:</div>
  <div class="date">October 20th - 31st, 2014</div>
</div>
<div class="ring" style="left:623px;top:2296px">
  <svg style="margin-top:42px" width="110" height="96" viewBox="0 0 110 96" fill="none" stroke="#fff" stroke-width="4"><circle cx="28" cy="24" r="20"/><circle cx="82" cy="24" r="20"/><line x1="20" y1="16" x2="36" y2="32"/><line x1="36" y1="16" x2="20" y2="32"/><polyline points="73,24 80,31 92,17"/><rect x="14" y="56" width="28" height="34" rx="3"/><rect x="68" y="56" width="28" height="34" rx="3"/><line x1="28" y1="44" x2="28" y2="56"/><line x1="82" y1="44" x2="82" y2="56"/></svg>
  <div class="head">ELECTION DAY:</div>
  <div class="date">November 4th, 2014</div>
</div>

<!-- donate -->
<div class="abs donate-bg"></div>
<svg class="slant" style="top:2680px" height="84" viewBox="0 2680 1200 84">
  <polygon points="0,2733 1200,2760 1200,2764 0,2764" fill="#f3f3f3"/>
  <polygon points="0,2683 780,2751 0,2733" fill="#ff6a1f"/>
</svg>
<svg class="abs" style="left:111px;top:2837px" width="166" height="144" viewBox="0 0 166 144" fill="none" stroke="#1c1c1c" stroke-width="6">
  <rect x="4" y="6" width="26" height="50"/>
  <path d="M30 14 Q70 0 110 6 Q150 14 158 44 Q160 56 146 56 L60 56"/>
  <path d="M30 48 L60 48"/>
  <circle cx="110" cy="102" r="36"/>
  <path d="M122 88 Q110 80 100 88 Q94 98 110 102 Q126 106 120 116 Q110 124 98 116"/>
  <line x1="110" y1="76" x2="110" y2="128"/>
  <line x1="56" y1="140" x2="164" y2="140"/>
</svg>
<h2 class="abs display" style="left:382px;top:2836px;font-size:42px">DONATE US</h2>
<div class="rule" style="left:383px;top:2898px;width:77px"></div>
<p class="abs donate-text">If you would like to contribute to this campaign, please click on the Donate button below to make an online donations.</p>
<a class="btn" style="left:383px;top:3020px;width:139px;height:53px">Donate Now</a>

<svg class="slant" style="top:3128px" height="74" viewBox="0 3128 1200 74">
  <polygon points="0,3202 1200,3185 1200,3202" fill="#fff"/>
  <polygon points="1200,3132 1200,3185 440,3185" fill="#ff6a1f"/>
</svg>
<div class="abs" style="left:0;top:3196px;width:1200px;height:209px;background:#fff"></div>

<!-- footer -->
<svg class="abs" style="left:111px;top:3245px" width="42" height="42" viewBox="0 0 42 42" fill="none" stroke="#1c1c1c" stroke-width="2"><circle cx="21" cy="21" r="19.5"/><path d="M21 32 Q12 22 12 17 A9 9 0 0 1 30 17 Q30 22 21 32 Z"/><circle cx="21" cy="17" r="3"/></svg>
<div class="abs footer-head">MAILING ADDRESS</div>
<div class="abs footer-addr">DANIELLE HARPER CAMPAIGN<br>PO Box 482190<br>Lakeview, Texas 75001<br>(555) 014-2283</div>

<a class="social" style="left:883px" aria-label="Social profile 1"></a>
<a class="social" style="left:937px" aria-label="Social profile 2"></a>
<a class="social" style="left:990px" aria-label="Social profile 3"></a>
<a class="social" style="left:1044px" aria-label="Social profile 4"></a>
<div class="abs" style="left:581px;top:3319px;width:507px;height:1px;background:#999"></div>
<div class="abs copyright">Copyrights @ 2019 Harper Danielle. All Rights Reserved.</div>

</body>
</html>
```